Lunelle Rosa Hair Fancy Business Card’s

I want my business cards to be elite, original and very classy. I want the business cards to match the colors of my logo and to match the design posted. I would love the design of the picture I posted

I want the card all white .
The dripping on the top of the card I want it to match the pink color in my logo that’s also posted .
I need my logo on the business card !
I need my Instagram- @lunelle.rosa.hair__
And my phone number - 555 207 3962

Target Market(s)

My target market is young woman age 23 to older woman to the age of 65
I want both older and younger women to love my design . I don’t want any cheap looking business cards

Industry/Entity Type

Hair And Beauty

Contact Information for Business Card

Add my logo
Add my Instagram- @lunelle.rosa.hair__
My number - 555 207 3962
My website- www.lunellerosahair.example

Font styles to use
Serif
Script

Colors
ffffff
e667a6
e34298

Requirements
Must have
• The business cards must have my logo, my number , my website, and my Instagram!
Nice to have
• Nice to have glitter words that match my logo
• The business cards must look classy and mature
• I want them to be very unique!!
Should not have
• Should not have any colors that doesn’t match my logo ! This is very important! Please

```html
<!DOCTYPE html>
<html lang="en">
<head>
<meta charset="utf-8">
<title>Lunelle Rosa Hair — Business Cards</title>
<link rel="stylesheet" href="https://fonts.googleapis.com/css2?family=Montserrat:wght@400;500&family=Great+Vibes&display=swap">
<style>
  :root {
    --backdrop: #3a3a3a;
    --card: #ffffff;
    --pink: #e34298;
    --pink-soft: #e667a6;
    --ink: #3b3b3b;
  }
  * { margin: 0; padding: 0; box-sizing: border-box; }
  html, body { width: 1200px; height: 901px; overflow: hidden; }
  body {
    background: var(--backdrop);
    font-family: "Montserrat", sans-serif;
    position: relative;
  }
  .card {
    position: absolute;
    left: 300px;
    width: 600px;
    height: 343px;
    background: var(--card);
    overflow: hidden;
  }
  .card--front { top: 87px; }
  .card--back { top: 470px; }
  .card__drip {
    position: absolute;
    left: 0; top: 0;
    width: 600px; height: 46px;
  }
  .card__band {
    position: absolute;
    left: 0; right: 0; bottom: 0;
    height: 14px;
    background: var(--pink);
  }
  .brand-name {
    font-family: "Montserrat", sans-serif;
    font-weight: 500;
    color: var(--pink);
    letter-spacing: 0.06em;
    text-transform: uppercase;
    text-align: center;
    line-height: 1.25;
  }
  .card--front .brand-name {
    position: absolute;
    left: 0; right: 0; top: 148px;
    font-size: 34px;
  }
  .card--back .brand-name {
    position: absolute;
    left: 40px; width: 230px; top: 132px;
    font-size: 24px;
  }
  .divider {
    position: absolute;
    left: 292px; top: 110px;
    width: 1.5px; height: 134px;
    background: var(--pink);
  }
  .contact {
    position: absolute;
    left: 318px; top: 104px;
  }
  .contact__name {
    font-family: "Great Vibes", cursive;
    color: var(--pink);
    font-size: 36px;
    line-height: 1;
  }
  .contact__role {
    color: var(--ink);
    font-size: 15px;
    margin: 2px 0 16px;
  }
  .contact__list { list-style: none; }
  .contact__item {
    display: flex;
    align-items: center;
    gap: 10px;
    color: var(--ink);
    font-size: 16px;
    line-height: 1.55;
  }
  .contact__icon { width: 14px; height: 14px; flex: none; }
</style>
</head>
<body>
  <section class="card card--front">
    <svg class="card__drip" viewBox="0 0 600 46" aria-hidden="true">
      <path fill="#e34298" d="M0 0H600V14C590 14 586 18 586 26C586 34 578 34 578 26C578 18 570 14 540 14C500 14 496 18 496 34C496 44 484 44 484 34C484 18 478 14 440 14C390 14 386 18 386 24C386 30 378 30 378 24C378 18 370 14 320 14C282 14 278 18 278 38C278 48 264 48 264 38C264 18 258 14 220 14C170 14 166 18 166 28C166 36 156 36 156 28C156 18 150 14 110 14C74 14 70 18 70 32C70 42 58 42 58 32C58 18 52 14 30 14H0Z"/>
    </svg>
    <p class="brand-name">Lunelle Rosa Hair</p>
    <div class="card__band"></div>
  </section>

  <section class="card card--back">
    <svg class="card__drip" viewBox="0 0 600 46" aria-hidden="true">
      <path fill="#e34298" d="M0 0H600V14C590 14 586 18 586 26C586 34 578 34 578 26C578 18 570 14 540 14C500 14 496 18 496 34C496 44 484 44 484 34C484 18 478 14 440 14C390 14 386 18 386 24C386 30 378 30 378 24C378 18 370 14 320 14C282 14 278 18 278 38C278 48 264 48 264 38C264 18 258 14 220 14C170 14 166 18 166 28C166 36 156 36 156 28C156 18 150 14 110 14C74 14 70 18 70 32C70 42 58 42 58 32C58 18 52 14 30 14H0Z"/>
    </svg>
    <p class="brand-name">Lunelle Rosa Hair</p>
    <div class="divider"></div>
    <div class="contact">
      <p class="contact__name">Delphine Marsh</p>
      <p class="contact__role">Manager</p>
      <ul class="contact__list">
        <li class="contact__item">
          <svg class="contact__icon" viewBox="0 0 24 24" aria-hidden="true"><path fill="#e34298" d="M6.6 10.8a15.1 15.1 0 0 0 6.6 6.6l2.2-2.2a1 1 0 0 1 1-.25 11.4 11.4 0 0 0 3.6.57 1 1 0 0 1 1 1V20a1 1 0 0 1-1 1A17 17 0 0 1 3 4a1 1 0 0 1 1-1h3.5a1 1 0 0 1 1 1c0 1.25.2 2.45.57 3.57a1 1 0 0 1-.25 1z"/></svg>
          555 207 3962
        </li>
        <li class="contact__item">
          <svg class="contact__icon" viewBox="0 0 14 14" aria-hidden="true"><rect x="1" y="1" width="12" height="12" rx="2" fill="#e34298"/></svg>
          @lunelle.rosa.hair__
        </li>
        <li class="contact__item">
          <svg class="contact__icon" viewBox="0 0 14 14" aria-hidden="true"><circle cx="7" cy="7" r="6" fill="#e34298"/></svg>
          www.lunellerosahair.example
        </li>
      </ul>
    </div>
    <div class="card__band"></div>
  </section>
</body>
</html>
```